FernPath....... a dash of Glow

I need a web design for a new business based in London that will be mobile (offered at homes, parks or a local cafe ect) called FernPath. I offer Life Coaching/Counselling sessions, Personal training, Massage and Sports Massage. Sessions range from an hour to half and hour. My aim is to help people along their journey to help give them gain clarity of where there going, helping them to towards their goals, so that can experience bliss. My website should represent a place people can come to release their stress and worries so that they leave feeling lighter, clearer and happier. I would like my website to reflect someone feeling ALIVE. I would also like a logo design for FernPath with a sentence underneath or near saying a touch of bliss.

Target Market(s)

middle class people

Industry/Entity Type

Business

Coding

Coded - Design and coding required

Number of Pages Required

4 page

Requirements
Must have
• 1st page About us
• 2nd page Services
• 3rd page Prices
• 4th page contact details
Nice to have
• mixture of cultures in images

```html
<!DOCTYPE html>
<html lang="en">
<head>
<meta charset="utf-8">
<title>FernPath — a dash of Glow</title>
<link href="https://fonts.googleapis.com/css2?family=Kumbh+Sans:wght@400;600;700&family=Open+Sans:ital,wght@0,400;0,600;1,400&display=swap" rel="stylesheet">
<style>
:root{
  --orange:#f3821f;
  --ink:#333;
  --muted:#555;
  --grey-ring:#a9a9a9;
  --panel:#f4f4f4;
  --footer:#2f2f2f;
  --footer-base:#262626;
  --footer-text:#a9a9a9;
  --white:#fff;
  --black:#000;
}
*{box-sizing:border-box;margin:0;padding:0}
html,body{width:668px;height:1200px;overflow:hidden;background:var(--white)}
body{position:relative;font-family:"Open Sans",Arial,sans-serif;color:var(--ink)}
.head-font{font-family:"Kumbh Sans","Helvetica Neue",sans-serif}
.abs{position:absolute}

/* header */
.site-header{position:absolute;left:0;top:0;width:668px;height:75px;border-top:2px solid var(--orange);background:var(--white);box-shadow:0 1px 3px rgba(0,0,0,.12);z-index:2}
.brand{left:55px;top:22px;font-family:"Kumbh Sans",sans-serif;color:var(--orange);font-size:16px;font-weight:400;letter-spacing:.5px}
.brand-tag{left:56px;top:43px;font-family:"Kumbh Sans",sans-serif;font-size:8px;letter-spacing:.6px;color:var(--ink)}
.contact-item{top:14px;display:flex;align-items:center;gap:5px;font-family:"Kumbh Sans",sans-serif;font-size:7.6px;color:var(--ink);white-space:nowrap}
.contact-item .ring{width:20px;height:20px;border:1.3px solid var(--orange);border-radius:50%;display:flex;align-items:center;justify-content:center}
.main-nav{left:245px;top:46px;width:351px;display:flex;justify-content:space-between;font-family:"Kumbh Sans",sans-serif;font-size:8.6px;letter-spacing:.4px;white-space:nowrap}
.main-nav a{color:var(--ink);text-decoration:none;position:relative;height:27px;padding-top:1px}
.main-nav a.is-current{color:var(--orange)}
.main-nav a.is-current::after{content:"";position:absolute;left:-2px;right:-2px;bottom:-2px;height:3px;background:var(--orange)}

/* hero */
.hero{left:0;top:75px;width:668px;height:273px;background:linear-gradient(100deg,#f3ecc7 0%,#efe0b4 35%,#d8b98f 55%,#9c8067 75%,#7a7066 100%)}
.hero-title{left:56px;top:148px;font-size:23px;font-weight:700;color:var(--orange);letter-spacing:.3px}
.hero-text{left:57px;top:181px;width:200px;font-size:6.8px;line-height:12px;color:var(--ink)}
.btn{display:inline-block;background:var(--orange);color:var(--white);font-family:"Kumbh Sans",sans-serif;font-size:8px;text-align:center;border-radius:2px}
.hero-btn{left:55px;top:215px;width:67px;height:23px;line-height:23px}
.dots{left:56px;top:253px;display:flex;gap:4px}
.dots span{width:4px;height:4px;border-radius:50%;border:1px solid var(--muted)}
.dots span.on{background:var(--orange);border-color:var(--orange)}

/* booking */
.booking{left:0;top:348px;width:668px;height:82px;background:var(--orange)}
.booking-title{left:55px;top:14px;font-size:11.5px;font-weight:600;color:var(--white);letter-spacing:.4px}
.field{top:36px;width:110px;height:24px;background:var(--white);border-radius:2px;font-size:6px;color:var(--ink);padding:8px 0 0 8px;letter-spacing:.3px}
.submit{left:525px;top:36px;width:89px;height:24px;background:var(--black);color:var(--white);font-size:7.5px;text-align:center;line-height:24px;border-radius:2px}

/* welcome */
.section-title{width:668px;left:0;text-align:center;font-size:14px;font-weight:700;color:var(--orange);letter-spacing:.3px}
.welcome-text{left:50px;top:476px;width:568px;text-align:center;font-size:6.6px;line-height:12px;color:var(--muted)}
.welcome-btn{left:302px;top:506px;width:64px;height:27px;line-height:27px}

/* services */
.services{left:0;top:555px;width:668px;height:251px;background:var(--panel)}
.service{top:0;width:190px;text-align:center}
.service .ring{margin:41px auto 0;width:75px;height:75px;border:4px solid var(--grey-ring);border-radius:50%;display:flex;align-items:center;justify-content:center}
.service h3{margin-top:17px;font-size:14px;font-weight:700;color:var(--orange);letter-spacing:.3px;white-space:nowrap}
.service p{margin:9px auto 0;width:172px;font-size:6.6px;line-height:12px;color:var(--muted)}
.service .read-more{margin-top:10px;font-family:"Kumbh Sans",sans-serif;font-size:6px;font-weight:700;color:var(--orange);letter-spacing:.3px}

/* testimonials */
.quote{top:865px;width:179px;height:92px;background:var(--panel);padding:10px 7px;font-size:6.4px;line-height:12px;color:var(--muted);text-align:justify}
.quote p+p{margin-top:7px}
.quote::after{content:"";position:absolute;right:37px;bottom:-12px;border-left:10px solid var(--panel);border-bottom:12px solid transparent}
.quote-name{top:972px;font-size:6.4px;font-style:italic;color:var(--orange)}

/* footer */
.site-footer{left:0;top:1004px;width:668px;height:160px;background:var(--footer);border-top:2px solid var(--orange)}
.foot-title{top:20px;font-size:11.5px;font-weight:600;color:var(--white);letter-spacing:.4px}
.foot-links{left:55px;top:52px;list-style:none;font-size:6.8px;line-height:15.8px;color:#cfcfcf}
.foot-text{font-size:6.6px;line-height:11.5px;color:var(--footer-text)}
.mail-field{left:164px;top:75px;width:123px;height:22px;background:var(--white);border-radius:2px;display:flex;align-items:center;gap:7px;padding-left:7px;font-size:6.2px;color:var(--ink)}
.foot-submit{left:163px;top:105px;width:38px;height:17px;background:var(--black);color:var(--white);font-size:6.6px;text-align:center;line-height:17px;border-radius:2px}
.foot-brand{left:530px;top:18px;font-family:"Kumbh Sans",sans-serif;font-size:16px;color:#8d8d8d;letter-spacing:.5px}
.social{top:46px;width:25px;height:25px;border:1px solid #777;border-radius:50%}
.base-bar{left:0;top:1164px;width:668px;height:36px;background:var(--footer-base);text-align:center;font-size:6.4px;line-height:36px;color:#8a8a8a}
</style>
</head>
<body>

<header class="site-header">
  <div class="abs brand">FERNPATH</div>
  <div class="abs brand-tag">A DASH OF GLOW</div>

  <div class="abs contact-item" style="left:420px">
    <span class="ring"><svg width="10" height="10" viewBox="0 0 24 24"><path fill="#f3821f" d="M6.6 10.8a15 15 0 0 0 6.6 6.6l2.2-2.2c.3-.3.7-.4 1-.2 1.1.4 2.3.6 3.6.6.6 0 1 .4 1 1V20c0 .6-.4 1-1 1A17 17 0 0 1 3 4c0-.6.4-1 1-1h3.5c.6 0 1 .4 1 1 0 1.3.2 2.5.6 3.6.1.3 0 .7-.2 1z"/></svg></span>
    0207 946 0321
  </div>
  <div class="abs contact-item" style="left:507px">
    <span class="ring"><svg width="10" height="8" viewBox="0 0 20 14"><rect x="1" y="1" width="18" height="12" rx="1.5" fill="none" stroke="#f3821f" stroke-width="1.8"/><path d="M1.5 2 10 8l8.5-6" fill="none" stroke="#f3821f" stroke-width="1.8"/></svg></span>
    hello@fernpath-mail.co
  </div>

  <nav class="abs main-nav">
    <a class="is-current">HOME</a>
    <a>ABOUT US</a>
    <a>ABOUT US</a>
    <a>ABOUT US</a>
    <a>ABOUT US</a>
    <a>ABOUT US</a>
  </nav>
</header>

<section class="abs hero" role="img" aria-label="Photo of a woman with eyes closed enjoying warm evening sunlight outdoors"></section>
<h1 class="abs hero-title head-font">A DASH OF GLOW</h1>
<p class="abs hero-text">People along their journey to help give them gain clarity of where there going</p>
<span class="abs btn hero-btn">Learn More</span>
<div class="abs dots"><span class="on"></span><span></span><span></span></div>

<section class="abs booking">
  <h2 class="abs booking-title head-font">BOOK AN APPOINTMENT</h2>
  <div class="abs field" style="left:55px">NAME</div>
  <div class="abs field" style="left:172px">MAIL ID</div>
  <div class="abs field" style="left:289px">PHONE NUMBER</div>
  <div class="abs field" style="left:407px">DATE
    <svg class="abs" style="right:7px;top:8px" width="7" height="7" viewBox="0 0 10 10"><rect x="0.5" y="1.5" width="9" height="8" fill="none" stroke="#777"/><rect x="0.5" y="1.5" width="9" height="2.5" fill="#777"/></svg>
  </div>
  <div class="abs submit">Submit</div>
</section>

<h2 class="abs section-title head-font" style="top:449px">WELCOME TO FERNPATH</h2>
<p class="abs welcome-text">Nemo enim ipsam voluptatem quia voluptas sit aspernatur aut odit aut fugit, sed quia consequuntur magni dolores eos qui ratione voluptatem sequi nesciunt. Neque porro quisquam est, qui dolorem ipsum quia dolor sit amet, consectetur, adipisci velit, sed quia non numquam e</p>
<span class="abs btn welcome-btn">Learn More</span>

<section class="abs services">
  <div class="abs service" style="left:42px">
    <div class="ring"><svg width="34" height="34" viewBox="0 0 40 40"><circle cx="20" cy="20" r="14" fill="none" stroke="#f3821f" stroke-width="8"/><g stroke="#f4f4f4" stroke-width="3"><line x1="10" y1="10" x2="15" y2="15"/><line x1="30" y1="10" x2="25" y2="15"/><line x1="10" y1="30" x2="15" y2="25"/><line x1="30" y1="30" x2="25" y2="25"/></g></svg></div>
    <h3 class="head-font">LIFE COACHING</h3>
    <p>Neque porro quisquam est, qui dolorem ipsum quia dolor sit amet, consectetur, adipisci velit, sed quia non numquam eius modi tempora</p>
    <div class="read-more">READ MORE</div>
  </div>
  <div class="abs service" style="left:239px">
    <div class="ring"><svg width="34" height="30" viewBox="0 0 40 36"><path d="M3 4h22a2 2 0 0 1 2 2v12a2 2 0 0 1-2 2H12l-6 5v-5H3a2 2 0 0 1-2-2V6a2 2 0 0 1 2-2z" fill="#f3821f"/><path d="M30 12h7a2 2 0 0 1 2 2v11a2 2 0 0 1-2 2h-2v5l-6-5H17a2 2 0 0 1-2-2v-2h10a5 5 0 0 0 5-5z" fill="#f3821f"/></svg></div>
    <h3 class="head-font">COUNSELLING</h3>
    <p>Neque porro quisquam est, qui dolorem ipsum quia dolor sit amet, consectetur, adipisci velit, sed quia non numquam eius modi tempora</p>
    <div class="read-more">READ MORE</div>
  </div>
  <div class="abs service" style="left:434px">
    <div class="ring"><svg width="30" height="30" viewBox="0 0 40 40"><circle cx="20" cy="12" r="8" fill="#f3821f"/><path d="M5 37c0-9 6-15 15-15s15 6 15 15z" fill="#f3821f"/></svg></div>
    <h3 class="head-font">PERSONAL TRAINING</h3>
    <p>Neque porro quisquam est, qui dolorem ipsum quia dolor sit amet, consectetur, adipisci velit, sed quia non numquam eius modi tempora</p>
    <div class="read-more">READ MORE</div>
  </div>
</section>

<h2 class="abs section-title head-font" style="top:828px">WHAT ‘S OUR CLIENTS SAY</h2>
<div class="abs quote" style="left:55px"><p>Nemo enim ipsam voluptatem quia voluptas sit aspernatur aut odit aut fugit,</p><p>sed quia consequuntur magni dolores eos qui ratione voluptatem sequi nesciunt. Neque porro quisquam est, qui dolorem ipsum quia dolor sit amet,</p></div>
<div class="abs quote" style="left:245px"><p>Nemo enim ipsam voluptatem quia voluptas sit aspernatur aut odit aut fugit,</p><p>sed quia consequuntur magni dolores eos qui ratione voluptatem sequi nesciunt. Neque porro quisquam est, qui dolorem ipsum quia dolor sit amet,</p></div>
<div class="abs quote" style="left:436px"><p>Nemo enim ipsam voluptatem quia voluptas sit aspernatur aut odit aut fugit,</p><p>sed quia consequuntur magni dolores eos qui ratione voluptatem sequi nesciunt. Neque porro quisquam est, qui dolorem ipsum quia dolor sit amet,</p></div>
<div class="abs quote-name" style="left:177px">- Sam Rowe -</div>
<div class="abs quote-name" style="left:367px">- Sam Rowe -</div>
<div class="abs quote-name" style="left:557px">- Sam Rowe -</div>

<footer class="abs site-footer">
  <h3 class="abs foot-title head-font" style="left:55px">QUICK LINKS</h3>
  <ul class="abs foot-links">
    <li>Home</li><li>About Us</li><li>Services</li><li>Our Goals</li><li>Testimonials</li><li>Contact Us</li>
  </ul>

  <h3 class="abs foot-title head-font" style="left:164px">NEWSLETTER SUBSCRIBE</h3>
  <p class="abs foot-text" style="left:164px;top:46px;width:160px">Subscribe newsletter to receive the latest news and updates direct to your inbox.</p>
  <div class="abs mail-field">
    <svg width="12" height="9" viewBox="0 0 20 14"><rect width="20" height="14" rx="1.5" fill="#444"/><path d="M1 1.5 10 8l9-6.5" fill="none" stroke="#fff" stroke-width="1.5"/></svg>
    ENTER YOUR MAIL ID
  </div>
  <div class="abs foot-submit">Submit</div>

  <h3 class="abs foot-title head-font" style="left:341px">CONTACT US</h3>
  <p class="abs foot-text" style="left:341px;top:46px;width:160px">Nemo enim ipsam voluptatem quia voluptas sit aspernatur aut odit aut fugit</p>
  <p class="abs foot-text" style="left:341px;top:78px">0207 946 0321<br>hello@fernpath-mail.co</p>

  <div class="abs foot-brand">FERNPATH</div>
  <span class="abs social" style="left:527px"></span>
  <span class="abs social" style="left:559px"></span>
</footer>
<div class="abs base-bar">©2015 FernPath. All rights reserved.</div>

</body>
</html>
```